Software Development Consulting Company Needs Business Card Design

We need a new business card design for our consultants at Kestrel Works (kestrelworks.example). We are a small firm that provides high-end software development and methodology consulting to medium to large enterprise IT organizations.

Our logo uses Futura for the font and we would like to stick with navy blue and canary yellow for the logo colors. Attached are normal and reversed versions of our logos in illustrator format.
Updates

Hi Everyone, Thank yo very much for your amazing design ideas. I have created a poll for this project and our employees will be voting on the design they wish to use. We will be making a decision this Wednesday (October 22nd). Thanks again, Dale Hartwick

Industry/Entity Type

Business

```html
<!DOCTYPE html>
<html lang="en">
<head>
<meta charset="utf-8">
<title>Kestrel Works — Business Card</title>
<link rel="stylesheet" href="https://fonts.googleapis.com/css2?family=Open+Sans:wght@400;600;700&display=swap">
<style>
  :root {
    --navy: #1c4a72;
    --canary: #ffee00;
    --paper: #ffffff;
    --ink-grey: #555b61;
    --rule-grey: #b9bcc0;
    --backdrop: #e9eaee;
  }
  * { box-sizing: border-box; margin: 0; padding: 0; }
  html, body {
    width: 1200px; height: 980px; overflow: hidden;
    background: var(--backdrop);
    font-family: "Open Sans", Arial, sans-serif;
  }
  .sheet {
    position: relative; width: 1200px; height: 980px;
    display: flex; align-items: center; justify-content: center; gap: 40px;
  }
  .card {
    position: relative; width: 540px; height: 310px;
    border-radius: 24px; overflow: hidden;
    box-shadow: 0 6px 18px rgba(0,0,0,0.12);
  }
  .card-front { background: var(--paper); }
  .card-back { background: var(--canary); }

  .wave { position: absolute; inset: 0; }

  .brand {
    position: absolute; display: flex; align-items: center; gap: 9px;
    color: var(--navy); font-weight: 600; letter-spacing: 0.14em;
    text-transform: uppercase; white-space: nowrap;
  }
  .brand-dot {
    width: 22px; height: 22px; border-radius: 50%;
    border: 3px solid var(--navy); flex: none;
  }
  .card-front .brand { left: 30px; top: 84px; font-size: 18px; }

  .divider {
    position: absolute; left: 298px; top: 70px; width: 1px; height: 150px;
    background: linear-gradient(to bottom, transparent, var(--rule-grey) 30%, var(--rule-grey) 70%, transparent);
  }
  .contact { position: absolute; left: 318px; top: 78px; color: var(--ink-grey); }
  .contact-name { color: var(--navy); font-weight: 700; font-size: 20px; line-height: 1.1; }
  .contact-title { font-size: 14px; margin-bottom: 14px; }
  .contact-line { display: flex; align-items: center; gap: 7px; font-size: 13px; line-height: 1.55; white-space: nowrap; }
  .contact-line svg { width: 13px; height: 13px; flex: none; }
  .contact-line.plain { padding-left: 20px; }

  .card-back .brand { right: 56px; top: 124px; font-size: 24px; }
  .back-url {
    position: absolute; left: 44px; bottom: 56px;
    font-size: 17px; letter-spacing: 0.16em; color: var(--ink-grey);
  }
</style>
</head>
<body>
<main class="sheet">
  <section class="card card-front" aria-label="Business card front">
    <svg class="wave" viewBox="0 0 540 310" aria-hidden="true">
      <path d="M0,150 C100,205 230,285 470,310 L446,310 C220,290 90,220 0,166 Z" fill="var(--canary)"/>
      <path d="M0,176 C90,228 210,296 430,310 L0,310 Z" fill="var(--navy)"/>
      <path id="url-track" d="M20,228 C100,270 200,298 330,308" fill="none"/>
      <text font-family="Open Sans, Arial, sans-serif" font-size="13" letter-spacing="1" fill="#ffffff">
        <textPath href="#url-track" startOffset="30">www.kestrelworks.example</textPath>
      </text>
    </svg>

    <div class="brand"><span class="brand-dot"></span>Kestrel Works</div>

    <div class="divider"></div>

    <div class="contact">
      <p class="contact-name">Your Name</p>
      <p class="contact-title">Title</p>
      <p class="contact-line">
        <svg viewBox="0 0 16 16" aria-hidden="true"><circle cx="8" cy="8" r="7" fill="none" stroke="var(--navy)" stroke-width="1.6"/><path d="M5.5,4.5 L7,6.5 L6.2,7.5 C6.8,8.6 7.6,9.4 8.6,10 L9.6,9.2 L11.5,10.6 L10.6,11.8 C7.6,11.4 4.8,8.6 4.4,5.4 Z" fill="var(--navy)"/></svg>
        012-555-0189
      </p>
      <p class="contact-line">
        <svg viewBox="0 0 16 16" aria-hidden="true"><rect x="1.5" y="3.5" width="13" height="9" rx="1.5" fill="var(--navy)"/><path d="M2,4.5 L8,9 L14,4.5" fill="none" stroke="#ffffff" stroke-width="1.3"/></svg>
        info@kestrelworks.example
      </p>
      <p class="contact-line plain">Riverton + Lakeside, IL</p>
    </div>
  </section>

  <section class="card card-back" aria-label="Business card back">
    <div class="brand"><span class="brand-dot"></span>Kestrel Works</div>
    <p class="back-url">www.kestrelworks.example</p>
  </section>
</main>
</body>
</html>
```